Stationary Set Rebrand for Brennick

We are a Canadian Distribution and Service Company that was established in 1969. Over the past 5 decades we have expanded our business and have warehouses across Canada. We specialize in adhesive tapes, adhesives, films, safety, warehouse, shipping, janitorial and packaging supplies.

We have updated our logo design and would like a new corporate branding identity that includes a new fresh Stationary Set (Business Cards, Letterhead, Letterhead MS Word, Envelope, Presentation Folders, Email Signatures, Notepad Covers, etc.)

Target Market(s)

Industrial Business Sector

Font styles to use
Sans Serif

Colors
0054AA
0677BA
7BADD7
CADEEF
E8F1F8
0094D4
00A9DD
6FCCEA
C7EBF8
E9F6FB
00AB8E
00BBA5
67D7C9
C6EFE9
E9F9F6
EB3D1F
EC4F4E
F09395
F8D3D4
FCEDEE

Requirements
Should not have
• Colors not too light, darker colours preferred

```html
<!DOCTYPE html>
<html lang="en">
<head>
<meta charset="utf-8">
<title>Brennick Business Card</title>
<link rel="stylesheet" href="https://fonts.googleapis.com/css2?family=Michroma&family=Rajdhani:wght@500;700&display=swap">
<style>
  :root {
    --backdrop: #e4e4e4;
    --brand-red: #d71920;
    --ink: #1c1a1b;
    --paper: #ffffff;
  }
  * { margin: 0; padding: 0; box-sizing: border-box; }
  html, body {
    width: 1200px;
    height: 1200px;
    overflow: hidden;
    background: var(--backdrop);
  }
  .canvas {
    position: relative;
    width: 1200px;
    height: 1200px;
  }
  .card {
    position: absolute;
    left: 252px;
    width: 696px;
    height: 398px;
  }
  .card--front { top: 156px; background: var(--paper); }
  .card--back  { top: 652px; background: var(--brand-red); }

  .front__divider {
    position: absolute;
    left: 350px; top: 0;
    width: 8px; height: 100%;
    background: var(--ink);
  }
  .front__panel {
    position: absolute;
    left: 359px; top: 0; right: 0; bottom: 0;
    background: var(--brand-red);
    color: var(--paper);
  }
  .brand-name {
    position: absolute;
    font-family: "Rajdhani", sans-serif;
    font-weight: 700;
    line-height: 1;
    white-space: nowrap;
    transform: translate(-50%, -50%);
  }
  .card--front .brand-name {
    left: 180px; top: 194px;
    font-size: 62px;
    color: var(--ink);
  }
  .card--back .brand-name {
    left: 50%; top: 50%;
    font-size: 84px;
    color: var(--paper);
  }

  .contact {
    position: absolute;
    left: 36px; top: 96px;
    font-family: "Rajdhani", sans-serif;
    font-weight: 500;
    font-size: 18px;
    line-height: 21px;
    letter-spacing: 0.5px;
  }
  .contact__name {
    font-family: "Michroma", sans-serif;
    font-size: 19px;
    line-height: 24px;
    font-weight: 400;
    letter-spacing: 0.5px;
    -webkit-text-stroke: 0.8px var(--paper);
  }
  .contact__role { margin-top: 4px; }
  .contact__address { margin-top: 18px; }
  .contact__list { list-style: none; margin-top: 12px; }
  .contact__item {
    display: flex;
    align-items: center;
    height: 21px;
  }
  .contact__icon {
    width: 15px; height: 15px;
    margin-right: 13px;
    flex: none;
    fill: var(--paper);
  }
</style>
</head>
<body>
<main class="canvas">
  <section class="card card--front" aria-label="Business card front">
    <div class="brand-name">Brennick</div>
    <div class="front__divider"></div>
    <div class="front__panel">
      <div class="contact">
        <div class="contact__name">MARK ELLISON</div>
        <div class="contact__role">President</div>
        <div class="contact__address">4210 Birchwood Avenue<br>Halifax, Canada 58213</div>
        <ul class="contact__list">
          <li class="contact__item">
            <svg class="contact__icon" viewBox="0 0 16 16" aria-hidden="true"><path d="M3.2 1.2l2.3 2.6-1.2 1.6c.9 2 2.4 3.6 4.4 4.6l1.6-1.2 2.6 2.3-1.4 2.5C7 13.3 2.6 8.9 1 4.3z"/></svg>
            <span>736-512-8840</span>
          </li>
          <li class="contact__item">
            <svg class="contact__icon" viewBox="0 0 16 16" aria-hidden="true"><path d="M4 0h8a1 1 0 011 1v14a1 1 0 01-1 1H4a1 1 0 01-1-1V1a1 1 0 011-1zm1 2v10h6V2zm3 11a1 1 0 100 2 1 1 0 000-2z"/></svg>
            <span>736-290-4417</span>
          </li>
          <li class="contact__item">
            <svg class="contact__icon" viewBox="0 0 16 16" aria-hidden="true"><path d="M1 3h14v10H1zm1.5 1.2L8 8.6l5.5-4.4z"/></svg>
            <span>info@brennick.com</span>
          </li>
          <li class="contact__item">
            <svg class="contact__icon" viewBox="0 0 16 16" aria-hidden="true"><path d="M8 1a7 7 0 100 14A7 7 0 008 1zm0 1.5c.8 0 1.8 1.5 2.2 3.8H5.8C6.2 4 7.2 2.5 8 2.5zM2.6 7.2h3.1c0 .6 0 1.1.1 1.6H2.6a5.6 5.6 0 010-1.6zm7.7 0h3.1a5.6 5.6 0 010 1.6h-3.2c.1-.5.1-1 .1-1.6zM5.8 9.7h4.4C9.8 12 8.8 13.5 8 13.5S6.2 12 5.8 9.7z"/></svg>
            <span>www.brennick.com</span>
          </li>
        </ul>
      </div>
    </div>
  </section>

  <section class="card card--back" aria-label="Business card back">
    <div class="brand-name">Brennick</div>
  </section>
</main>
</body>
</html>
```